Business Card Design Can you design a business card design? Looking for something unique and differe

Can you design a business card design? Looking for something unique and different. Can you design a business card design? Looking for something unique and different.Can you design a business card design? Looking for something unique and different.Can you design a business card design? Looking for something unique and different.Can you design a business card design? Looking for something unique and different.Can you design a business card design? Looking for something unique and different.

Industry/Entity Type

Business

Contact Information for Business Card

Can you design a business card design? Looking for something unique and different.

Font styles to use
Serif

```html
<!DOCTYPE html>
<html lang="en">
<head>
<meta charset="utf-8">
<title>Meridose Business Card</title>
<link rel="stylesheet" href="https://fonts.googleapis.com/css2?family=Open+Sans:wght@400;600;700&display=swap">
<style>
  :root {
    --backdrop: #8e8e8e;
    --card-white: #ffffff;
    --brand-purple: #9b7baa;
    --brand-grey: #8a8a8a;
    --text-white: #ffffff;
  }
  * { margin: 0; padding: 0; box-sizing: border-box; }
  html, body {
    width: 1200px; height: 900px; overflow: hidden;
    background: var(--backdrop);
    font-family: "Open Sans", sans-serif;
  }
  .stage {
    position: relative; width: 1200px; height: 900px;
  }
  .card {
    position: absolute; left: 250px;
    width: 700px; height: 400px;
    background: var(--card-white);
    overflow: hidden;
    box-shadow: 0 6px 18px rgba(0,0,0,0.25);
  }
  .card-front { top: 30px; }
  .card-back { top: 470px; }

  .band { position: absolute; left: 0; width: 100%; background: var(--brand-purple); }
  .card-front .band-top { top: 0; height: 78px; }
  .card-front .band-bottom { top: 318px; height: 44px; }
  .card-back .band-main { top: 130px; height: 228px; }

  .brand {
    position: absolute; display: flex; align-items: center; gap: 12px;
    color: var(--brand-purple); font-weight: 600;
  }
  .brand-square { width: 26px; height: 26px; background: var(--brand-grey); }
  .card-front .brand { left: 50%; top: 170px; transform: translateX(-50%); font-size: 40px; }
  .card-back .brand { right: 36px; top: 46px; font-size: 34px; }
  .card-back .brand-square { width: 22px; height: 22px; }

  .person { position: absolute; left: 30px; top: 146px; color: var(--text-white); }
  .person-name { font-size: 27px; font-weight: 600; line-height: 1.1; }
  .person-title { font-size: 15px; font-weight: 400; }

  .contacts {
    position: absolute; right: 30px; top: 208px;
    list-style: none; text-align: right; color: var(--text-white);
    font-size: 18px; line-height: 28px;
  }
  .contacts li { display: flex; justify-content: flex-end; align-items: center; gap: 12px; }
  .contacts svg { width: 15px; height: 15px; fill: var(--text-white); flex: none; }
</style>
</head>
<body>
<main class="stage">
  <section class="card card-front" aria-label="Card front">
    <div class="band band-top"></div>
    <div class="brand"><span class="brand-square"></span><span class="brand-name">Meridose</span></div>
    <div class="band band-bottom"></div>
  </section>

  <section class="card card-back" aria-label="Card back">
    <div class="brand"><span class="brand-square"></span><span class="brand-name">Meridose</span></div>
    <div class="band band-main"></div>
    <div class="person">
      <p class="person-name">Elias Marlow</p>
      <p class="person-title">Managing Director</p>
    </div>
    <ul class="contacts">
      <li>555.014.2280
        <svg viewBox="0 0 16 16" aria-hidden="true"><path d="M2 5c0-2 2-3 6-3s6 1 6 3v1h-3V4.8C10 4.4 9 4.3 8 4.3s-2 .1-3 .5V6H2zM4 7h8l2 6H2z"/></svg></li>
      <li>555.014.2281
        <svg viewBox="0 0 16 16" aria-hidden="true"><path d="M4 1h7v4H4zM2 6h12v9H2zm3 2v2h2V8zm4 0v2h2V8zm-4 3v2h2v-2zm4 0v2h2v-2z"/></svg></li>
      <li>hello@meridose.example
        <svg viewBox="0 0 16 16" aria-hidden="true"><path d="M1 3h14v10H1zm1.5 1.5L8 9l5.5-4.5z"/></svg></li>
      <li>www.meridose.example
        <svg viewBox="0 0 16 16" aria-hidden="true"><path d="M6.5 9.5l3-3 1 1-3 3zM3 8l3-3 2 2-1 1-1-1-2 2 2 2 1-1 1 1-2 2a2.5 2.5 0 01-4-4zm10 0l-3 3-2-2 1-1 1 1 2-2-2-2-1 1-1-1 2-2a2.5 2.5 0 014 4z"/></svg></li>
      <li>48 Alder Row, Fenwick Bay, 30417
        <svg viewBox="0 0 16 16" aria-hidden="true"><path d="M8 1a5 5 0 015 5c0 4-5 9-5 9S3 10 3 6a5 5 0 015-5zm0 3a2 2 0 100 4 2 2 0 000-4z"/></svg></li>
    </ul>
  </section>
</main>
</body>
</html>
```